Business Broker Graphics Package

Hi,

Seeking a smart and professional graphics package design including business card design (double-sided) and letterhead and PowerPoint slide template.

3 Deliverables:

1. Company Letterhead
2. Business Card (two sided) (will consider one sided designs)
3. PowerPoint Template. Requires cover PPT and 2nd page design.

For the prototype use this info:
Marcus Dellorane RPA
Registered Practice Adviser
5678 Harlow Rd.
Marlow Bay, FL 77777
555.014.2273
Demo@Quillbrookpath.com
www.QuillbrookPath.com

I'll give exact information to winner to finalize later.

I've attached the logo..

Business card will be double sided and info for back of card is in attachment.

Look forward to your great ideas and concepts!

Target Market(s)

President's and business owners, CPA's and other professionals.

Industry/Entity Type

Business

Requirements
Nice to have
• Prefer horizontal card, but will consider vertical card design.

The business card should be all or primarily white. Text colors should be same as logo creative combination of black and forest green.

PowerPoint can be white background or lighter palette of colors I like gold color. I do not like darkly colored PowerPoint designs I prefer light and bright designs.

```html
<!DOCTYPE html>
<html lang="en">
<head>
<meta charset="utf-8">
<title>Quillbrook Path Business Card</title>
<link rel="stylesheet" href="https://fonts.googleapis.com/css2?family=Open+Sans:wght@400;600&family=Roboto+Condensed:wght@400&display=swap">
<style>
  :root {
    --backdrop: #9c9c9c;
    --card: #ffffff;
    --forest: #1f3d26;
    --ink: #2b2b2b;
    --muted: #555555;
    --rule: #cfcfcf;
    --faint: #e4e4e4;
  }
  html, body {
    margin: 0;
    width: 1200px;
    height: 1000px;
    overflow: hidden;
    background: var(--backdrop);
  }
  .card {
    position: absolute;
    left: 402px;
    top: 369px;
    width: 383px;
    height: 224px;
    background: var(--card);
    overflow: hidden;
  }
  .faint-rule {
    position: absolute;
    left: 0;
    top: 193px;
    width: 383px;
    height: 3px;
    background: var(--faint);
  }
  .brand-name {
    position: absolute;
    left: 26px;
    top: 56px;
    margin: 0;
    font-family: "Open Sans", sans-serif;
    font-weight: 600;
    font-size: 20px;
    line-height: 1.2;
    color: var(--forest);
    white-space: nowrap;
  }
  .divider {
    position: absolute;
    left: 24px;
    top: 103px;
    width: 211px;
    height: 1px;
    background: var(--rule);
  }
  .person-name {
    position: absolute;
    left: 226px;
    top: 73px;
    margin: 0;
    font-family: "Open Sans", sans-serif;
    font-weight: 400;
    font-size: 13px;
    color: var(--ink);
    white-space: nowrap;
  }
  .person-title {
    position: absolute;
    left: 243px;
    top: 96px;
    margin: 0;
    font-family: "Roboto Condensed", sans-serif;
    font-size: 10px;
    color: var(--ink);
    white-space: nowrap;
  }
  .contact-list {
    position: absolute;
    left: 23px;
    top: 116px;
    margin: 0;
    padding: 0;
    list-style: none;
    font-family: "Open Sans", sans-serif;
    font-size: 9.5px;
    color: var(--muted);
  }
  .contact-list li {
    display: flex;
    align-items: center;
    height: 16.5px;
    white-space: nowrap;
  }
  .contact-icon {
    width: 13px;
    height: 13px;
    margin-right: 5px;
    flex: none;
  }
  .slogan {
    position: absolute;
    left: 22px;
    top: 198px;
    margin: 0;
    font-family: "Open Sans", sans-serif;
    font-weight: 600;
    font-size: 10.5px;
    color: var(--forest);
    white-space: nowrap;
  }
</style>
</head>
<body>
  <div class="card">
    <div class="faint-rule"></div>

    <p class="brand-name">Quillbrook Path</p>
    <div class="divider"></div>

    <p class="person-name">Marcus Dellorane RPA</p>
    <p class="person-title">Registered Practice Adviser</p>

    <ul class="contact-list">
      <li>
        <svg class="contact-icon" viewBox="0 0 13 13" aria-hidden="true">
          <rect width="13" height="13" rx="1.5" fill="var(--forest)"/>
          <rect x="4" y="2" width="5" height="9" rx="1" fill="none" stroke="#fff" stroke-width="1"/>
          <circle cx="6.5" cy="9.3" r="0.6" fill="#fff"/>
        </svg>
        555.014.2273
      </li>
      <li>
        <svg class="contact-icon" viewBox="0 0 13 13" aria-hidden="true">
          <rect width="13" height="13" rx="1.5" fill="var(--forest)"/>
          <path d="M6.5 11 L3.8 6.6 A3 3 0 1 1 9.2 6.6 Z" fill="none" stroke="#fff" stroke-width="1"/>
          <circle cx="6.5" cy="5.2" r="1" fill="#fff"/>
        </svg>
        5678 Harlow Rd. Marlow Bay, FL 77777
      </li>
      <li>
        <svg class="contact-icon" viewBox="0 0 13 13" aria-hidden="true">
          <rect width="13" height="13" rx="1.5" fill="var(--forest)"/>
          <rect x="2.5" y="3.8" width="8" height="5.4" fill="none" stroke="#fff" stroke-width="1"/>
          <path d="M2.5 3.8 L6.5 6.8 L10.5 3.8" fill="none" stroke="#fff" stroke-width="1"/>
        </svg>
        Demo@Quillbrookpath.com
      </li>
      <li>
        <svg class="contact-icon" viewBox="0 0 13 13" aria-hidden="true">
          <rect width="13" height="13" rx="1.5" fill="var(--forest)"/>
          <circle cx="6.5" cy="6.5" r="3.8" fill="none" stroke="#fff" stroke-width="1"/>
          <ellipse cx="6.5" cy="6.5" rx="1.6" ry="3.8" fill="none" stroke="#fff" stroke-width="0.8"/>
          <line x1="2.7" y1="6.5" x2="10.3" y2="6.5" stroke="#fff" stroke-width="0.8"/>
        </svg>
        www.QuillbrookPath.com
      </li>
    </ul>

    <p class="slogan">Transition Guidance</p>
  </div>
</body>
</html>
```